Simple Business Card Design for Tavlo

Job:

Make a very simple, minimalist business card design with my details including adjusted logo. One side to be white (with logo & text). Other side to be yellow - try plain or with logo (or part of logo eg Z). Need business card to have continuity with website.

Logo:
Our logo is made from a free download font website:
http://www.typewell.net/search.php?q=rubber
but the spacing/kerning needs correcting/adjusting as the font spaces unevenly between letters (see attached files). Need logo to be very crisp/sharp when printed.

Printing:
We will be using Plika.com so the design needs to conform to their requirements, see here:

http://uk.plika.com/products/luxe/business-cards.html (scroll down for dimensions and guidelines)

Design:

must say "plant-based food consulting" underneath logo or somewhere
no address needed in contact section
sharp corners (not rounded)
one side white, one side yellow

name: Rosalind Whitcombe
1xmobile number: +44 7700900463
1xtwiiter: @brimcounsel
website address www.orchardtable.com
email address brim@orchardtable.com

Should be easy quick job, prompt + detailed feedback given, am online in UK 9am-10pm for next 3 days. Website is www.orchardtable.com

Industry/Entity Type

Business

Requirements
Must have
• The logo must be corrected. The kerning is not right.

Please use a warm-grey for text

Please submit in matt format, we will be printing matt finish.

Should not have
• Avoid using banners or curvy highlights

Please avoid using black

Please avoid submitting in gloss finish

```html
<!DOCTYPE html>
<html lang="en">
<head>
<meta charset="utf-8">
<title>Tavlo Business Card</title>
<link rel="stylesheet" href="https://fonts.googleapis.com/css2?family=Cinzel:wght@400;700&display=swap">
<style>
  :root {
    --backdrop: #e7e7e7;
    --card-white: #ffffff;
    --card-yellow: #f2df4a;
    --accent: #d9bf1f;
    --warm-grey: #6f6760;
    --warm-grey-dark: #5a534d;
  }
  * { margin: 0; padding: 0; box-sizing: border-box; }
  html, body {
    width: 1200px;
    height: 720px;
    overflow: hidden;
    background: var(--backdrop);
  }
  .canvas {
    position: relative;
    width: 1200px;
    height: 720px;
    font-family: "Cinzel", serif;
  }
  .card {
    position: absolute;
    top: 242px;
    width: 420px;
    height: 240px;
  }
  .card--front { left: 147px; background: var(--card-white); }
  .card--back { left: 633px; background: var(--card-yellow); }

  .brand {
    display: flex;
    align-items: center;
    gap: 10px;
  }
  .brand-square {
    width: 12px;
    height: 12px;
    background: var(--accent);
  }
  .wordmark {
    color: var(--warm-grey-dark);
    font-weight: 400;
    letter-spacing: 0.04em;
    line-height: 1;
  }
  .tagline {
    color: var(--warm-grey);
    font-size: 9px;
    letter-spacing: 0.14em;
    line-height: 1;
  }
  .card--front .brand-block {
    position: absolute;
    left: 21px;
    top: 26px;
  }
  .card--front .wordmark { font-size: 46px; }
  .card--front .tagline { margin-top: 8px; }

  .card--back .brand-block {
    position: absolute;
    left: 0;
    right: 0;
    top: 50%;
    transform: translateY(-50%);
    text-align: center;
  }
  .card--back .wordmark { font-size: 68px; }
  .card--back .tagline { margin-top: 10px; font-size: 11px; color: var(--warm-grey-dark); }

  .contact-list {
    position: absolute;
    left: 21px;
    top: 168px;
    list-style: none;
  }
  .contact-list li {
    display: flex;
    align-items: center;
    height: 13px;
    font-size: 9px;
    color: var(--warm-grey);
    letter-spacing: 0.02em;
  }
  .contact-list svg {
    width: 10px;
    height: 9px;
    margin-right: 8px;
    fill: none;
    stroke: var(--accent);
  }
  .contact-list .icon-fill { fill: var(--accent); stroke: none; }

  .holder {
    position: absolute;
    right: 20px;
    top: 190px;
    text-align: right;
  }
  .holder-name {
    color: var(--warm-grey-dark);
    font-weight: 700;
    font-size: 12px;
    line-height: 1.2;
  }
  .holder-role {
    color: var(--warm-grey);
    font-size: 9.5px;
    line-height: 1.3;
  }
</style>
</head>
<body>
<main class="canvas">
  <section class="card card--front">
    <div class="brand-block">
      <div class="brand">
        <span class="wordmark">Tavlo</span>
        <span class="brand-square"></span>
      </div>
      <div class="tagline">plant-based food consulting</div>
    </div>
    <ul class="contact-list">
      <li>
        <svg viewBox="0 0 10 9" aria-hidden="true"><path class="icon-fill" d="M0 3 Q5 0 10 3 L9 4 L7 3 L6.5 2.5 L3.5 2.5 L3 3 L1 4 Z M2.5 4 L7.5 4 L9 8 L1 8 Z"/></svg>
        +44 7700 900463
      </li>
      <li>
        <svg viewBox="0 0 10 9" aria-hidden="true"><path class="icon-fill" d="M0 1 L10 1 L10 8 L0 8 Z"/><path d="M0.5 1.5 L5 5 L9.5 1.5 M0.5 7.5 L4 4.5 M9.5 7.5 L6 4.5" stroke="var(--card-white)" stroke-width="0.8"/></svg>
        brim@orchardtable.com
      </li>
      <li>
        <svg viewBox="0 0 10 9" aria-hidden="true"><path d="M1 1 L9 1 L9 6 L4 6 L2 8 L2 6 L1 6 Z" stroke-width="1.1"/></svg>
        @brimcounsel
      </li>
      <li>
        <svg viewBox="0 0 10 9" aria-hidden="true"><rect x="0.6" y="0.6" width="8.8" height="5.8" stroke-width="1.1"/><path class="icon-fill" d="M3 7.4 L7 7.4 L7 8.6 L3 8.6 Z"/></svg>
        www.orchardtable.com
      </li>
    </ul>
    <div class="holder">
      <div class="holder-name">Rosalind Whitcombe</div>
      <div class="holder-role">Manager</div>
    </div>
  </section>

  <section class="card card--back">
    <div class="brand-block">
      <div class="wordmark">Tavlo</div>
      <div class="tagline">plant-based food consulting</div>
    </div>
  </section>
</main>
</body>
</html>
```